Stock certificate

We need a stock certificate with a modern design aligned with our company background (Consulting & IT-Services Company with innovation drive).
The certificate should include our logo and should have some space to insert our dedicated text (value, issuer, etc.).
Format should be A4 landscape. The page must be workable, meaning that the background of the certificate can be fixed (kind of master), but the front where the text shall be written must be flexible. PPT-format could make it for example.
Orvix font style desired.
Required text areas are shown in the uploaded example.
Orvix font style would be great.
It Company

```html
<!DOCTYPE html>
<html lang="en">
<head>
<meta charset="utf-8">
<title>Veltrano – Stock Certificate</title>
<link rel="stylesheet" href="https://fonts.googleapis.com/css2?family=Nunito+Sans:wght@300;700&display=swap">
<style>
  :root {
    --paper: #ffffff;
    --sky-light: #e6eef6;
    --blue-soft: #9cc3e3;
    --blue-mid: #3f8fcc;
    --blue-deep: #1d5f96;
    --navy: #14324d;
    --ink: #2b2b2b;
    --wordmark: #3b3e44;
  }

  html, body {
    margin: 0;
    padding: 0;
    width: 1200px;
    height: 848px;
    overflow: hidden;
    background: var(--paper);
  }

  .certificate {
    position: relative;
    width: 1200px;
    height: 848px;
    overflow: hidden;
    font-family: "Nunito Sans", "Helvetica Neue", Arial, sans-serif;
    color: var(--ink);
  }

  .certificate__artwork {
    position: absolute;
    inset: 0;
    background:
      radial-gradient(ellipse 260px 90px at 280px 50px, rgba(255,255,255,0.95), rgba(255,255,255,0) 100%),
      radial-gradient(ellipse 520px 260px at 1000px 640px, var(--paper) 30%, rgba(255,255,255,0) 100%),
      radial-gradient(ellipse 420px 220px at 900px 170px, rgba(20,50,77,0.55), rgba(20,50,77,0) 100%),
      linear-gradient(160deg,
        var(--sky-light) 0%,
        var(--blue-soft) 22%,
        var(--blue-mid) 40%,
        var(--blue-deep) 52%,
        var(--blue-mid) 62%,
        var(--blue-soft) 74%,
        var(--paper) 90%);
  }

  .field {
    position: absolute;
    margin: 0;
    font-weight: 300;
    font-size: 23px;
    letter-spacing: 0.2px;
    color: var(--ink);
  }

  .field--number { left: 36px; top: 38px; }
  .field--stock  { left: 28px; top: 140px; }

  .brand {
    position: absolute;
    left: 766px;
    top: 669px;
    margin: 0;
    font-weight: 700;
    font-size: 82px;
    line-height: 1;
    letter-spacing: 6px;
    color: var(--wordmark);
    white-space: nowrap;
  }
</style>
</head>
<body>
  <main class="certificate">
    <div class="certificate__artwork" role="img" aria-label="Abstract background of flowing translucent blue ribbons and fine line-mesh curves sweeping across the page"></div>

    <p class="field field--number">Certificate no:</p>
    <p class="field field--stock">Common Stock:</p>

    <p class="brand">Veltrano</p>
  </main>
</body>
</html>
```